Global (re)insurance broker needs a business card design

We need a classic business card for our company that is headquartered in SG, with offices in Malaysia and Dubai. We specialise in insurance and reinsurance broking and consultancy for our global clients.

```html
<!DOCTYPE html>
<html lang="en">
<head>
<meta charset="utf-8">
<title>Veracrest Business Card</title>
<link rel="stylesheet" href="https://fonts.googleapis.com/css2?family=Open+Sans:wght@400;600;700&display=swap">
<style>
  :root {
    --backdrop: #2b2b2f;
    --card-dark: #1f1f23;
    --emboss: #141417;
    --brand-blue: #2b4fb8;
    --brand-blue-deep: #1d3a9e;
    --brand-blue-light: #3560d0;
    --mint: #bcd9b8;
    --ink-light: #eef0f2;
  }
  * { box-sizing: border-box; margin: 0; padding: 0; }
  html, body { width: 1200px; height: 780px; overflow: hidden; }
  body {
    background: var(--backdrop);
    font-family: "Open Sans", Arial, sans-serif;
    position: relative;
  }
  .card {
    position: absolute;
    top: 235px;
    width: 540px;
    height: 310px;
    border-radius: 3px;
    overflow: hidden;
    box-shadow: 0 14px 30px rgba(0,0,0,0.45);
  }
  .card-front { left: 40px; background: var(--card-dark); }
  .card-back { left: 620px; }

  .front-wordmark {
    position: absolute;
    left: 28px; top: 20px;
    font-size: 50px; font-weight: 600;
    color: var(--mint);
    letter-spacing: 1px;
    line-height: 1;
  }
  .contact {
    position: absolute;
    left: 28px; top: 108px;
    color: var(--ink-light);
    font-size: 13px;
    line-height: 1.45;
  }
  .contact-address { margin-bottom: 4px; }
  .contact-line { display: flex; align-items: center; gap: 7px; font-size: 12.5px; }
  .contact-line svg { width: 11px; height: 11px; flex: none; }

  .person {
    position: absolute;
    right: 40px; top: 150px;
    text-align: right;
  }
  .person-name {
    font-size: 28px; font-weight: 700;
    color: var(--brand-blue);
    line-height: 1.1;
  }
  .person-title {
    font-size: 14.5px;
    color: var(--ink-light);
    margin-top: 2px;
  }
  .accent-bar {
    position: absolute;
    right: 0; top: 140px;
    width: 20px; height: 58px;
    background: var(--mint);
  }
  .emboss-wordmark {
    position: absolute;
    right: 40px; bottom: 4px;
    font-size: 64px; font-weight: 600;
    color: var(--emboss);
    line-height: 1;
    letter-spacing: 1px;
  }

  .back-field {
    position: absolute; inset: 0;
    background: linear-gradient(115deg, var(--brand-blue-deep) 0%, var(--brand-blue) 55%, var(--brand-blue-light) 100%);
  }
  .back-wordmark {
    position: absolute;
    left: 250px; top: 232px;
    font-size: 17px; font-weight: 600;
    color: var(--ink-light);
    letter-spacing: 0.5px;
  }
</style>
</head>
<body>
  <section class="card card-front">
    <div class="front-wordmark">Veracrest</div>

    <div class="contact">
      <p class="contact-address">24 Harbour Lane, Meridian<br>Tower #08-03, Singapore 018956</p>
      <p class="contact-line">
        <svg viewBox="0 0 12 12"><rect x="3" y="0.8" width="6" height="10.4" rx="1.2" fill="none" stroke="#bcd9b8" stroke-width="1.2"/></svg>
        +65 9123 4567
      </p>
      <p class="contact-line">
        <svg viewBox="0 0 12 12"><circle cx="6" cy="6" r="5" fill="none" stroke="#3560d0" stroke-width="1.2"/><path d="M1 6h10M6 1c-2.5 3-2.5 7 0 10M6 1c2.5 3 2.5 7 0 10" fill="none" stroke="#3560d0" stroke-width="1"/></svg>
        www.veracrest.com
      </p>
      <p class="contact-line">
        <svg viewBox="0 0 12 12"><rect x="0.8" y="2.5" width="10.4" height="7" rx="1" fill="none" stroke="#bcd9b8" stroke-width="1.2"/><path d="M1 3l5 4 5-4" fill="none" stroke="#bcd9b8" stroke-width="1.1"/></svg>
        mira@veracrest.com
      </p>
    </div>

    <div class="person">
      <h1 class="person-name">Mira Lowe</h1>
      <p class="person-title">Chief Operating Officer</p>
    </div>
    <div class="accent-bar"></div>

    <div class="emboss-wordmark" aria-hidden="true">Veracrest</div>
  </section>

  <section class="card card-back">
    <div class="back-field" role="img" aria-label="Repeating pattern of the company name in tonal blues, fading lighter toward the upper right"></div>
    <div class="back-wordmark">Veracrest</div>
  </section>
</body>
</html>
```